Quorbelline.io - Please redesign to make it look better from current design

We already have the current website, that you can access but we think it can improve from current version.
Quorbelline is a cryptocurrency hedge fund that allow you to participate in the hedge fund with cryptocurrency such as eth.
At current phase, we are doing an ICO, then we want to make sure that the website it looks professional, beautiful and trustable enough for investors after looking at our website.
Target Market(s)
Investors
Industry/Entity Type
Investment
Coding
Coded - Design and coding required
Number of Pages Required
1 page
Look and feel
Each slider illustrates characteristics of the customer's brand and the style your logo design should communicate.

```html
<!DOCTYPE html>
<html lang="en">
<head>
<meta charset="utf-8">
<title>Quorbelline – Digital Asset Management</title>
<link href="https://fonts.googleapis.com/css2?family=Raleway:wght@500;600;700&family=Open+Sans:wght@400;600;700&display=swap" rel="stylesheet">
<style>
:root{
  --navy:#0d3f8f;
  --blue:#1f64b8;
  --sky:#2f9fd8;
  --ink:#1d1d1d;
  --grey:#6b6b6b;
  --footer:#1f2124;
  --white:#ffffff;
}
*{margin:0;padding:0;box-sizing:border-box}
html,body{width:1200px;height:3136px;overflow:hidden;background:var(--white)}
body{position:relative;font-family:"Open Sans",Arial,sans-serif;color:var(--ink)}
.abs{position:absolute}

/* header */
.site-header{left:0;top:0;width:1200px;height:100px;background:var(--white);border-top:4px solid var(--navy)}
.brand{left:98px;top:24px;display:flex;align-items:center;gap:12px}
.brand-dot{width:40px;height:40px;border-radius:50%;background:var(--navy)}
.brand-name{font-family:"Raleway",sans-serif;font-weight:700;font-size:24px;color:var(--navy)}
.contact-top{top:16px;display:flex;align-items:center;gap:10px;font-size:15px;color:var(--ink)}
.icon-ring{width:32px;height:32px;border-radius:50%;border:1.5px solid var(--sky);display:flex;align-items:center;justify-content:center}
.main-nav{right:80px;top:66px;display:flex;align-items:center;gap:34px;font-family:"Raleway",sans-serif;font-weight:600;font-size:16px;color:var(--ink)}

/* hero */
.hero{left:0;top:100px;width:1200px;height:500px;
  background:
    linear-gradient(180deg,rgba(0,0,0,0) 0%,rgba(0,0,0,0) 62%,rgba(20,40,60,.35) 100%),
    linear-gradient(180deg,#8fb0cc 0%,#a9bfd2 22%,#7d90a3 40%,#5b6c7e 55%,#3d4f60 66%,#6f8ea8 72%,#4e6f8b 82%,#2f5069 100%)}
.hero-title{left:0;top:236px;width:1200px;text-align:center;font-family:"Raleway",sans-serif;font-weight:700;font-size:50px;color:var(--white);text-shadow:0 2px 6px rgba(0,0,0,.35)}
.hero-sub{left:0;top:309px;width:1200px;text-align:center;font-size:21px;line-height:34px;color:var(--white);text-shadow:0 1px 4px rgba(0,0,0,.4)}
.btn-solid{left:505px;top:398px;width:190px;height:52px;border-radius:26px;background:var(--sky);color:var(--white);font-weight:700;font-size:16px;display:flex;align-items:center;justify-content:center}
.slider-dots{left:563px;top:537px;display:flex;gap:6px}
.slider-dots span{width:13px;height:13px;border-radius:50%;border:2px solid var(--white)}
.slider-dots span.on{background:var(--white)}

/* welcome */
.welcome-title{left:98px;top:682px;font-family:"Raleway",sans-serif;font-weight:700;font-size:31px;color:var(--ink)}
.welcome-text{left:98px;top:740px;width:470px;font-size:12.5px;line-height:22px;color:var(--grey)}
.welcome-text p{margin-bottom:22px}
.btn-outline{height:38px;border-radius:19px;border:1.5px solid #b9c4d2;color:var(--sky);font-weight:700;font-size:12.5px;display:flex;align-items:center;justify-content:center;background:var(--white)}
.video-frame{left:607px;top:690px;width:494px;height:313px;border:4px solid var(--white);box-shadow:0 0 0 1px #d8dde4,0 4px 10px rgba(0,0,0,.12);
  background:
    radial-gradient(ellipse at 70% 65%,rgba(120,230,200,.55) 0%,rgba(0,0,0,0) 55%),
    radial-gradient(ellipse at 25% 20%,rgba(160,220,255,.45) 0%,rgba(0,0,0,0) 50%),
    linear-gradient(160deg,#16455f 0%,#1f7a86 45%,#2b9a86 62%,#0f3350 100%)}
.play{left:210px;top:120px;width:60px;height:60px;border-radius:50%;background:rgba(20,20,20,.85)}

/* services */
.services-band{left:0;top:1097px;width:1200px;height:188px;background:linear-gradient(180deg,#0c49a3 0%,#1560bf 100%)}
.services-title{left:0;top:1142px;width:1200px;text-align:center;font-family:"Raleway",sans-serif;font-weight:700;font-size:29px;color:var(--white)}
.service{top:1216px;width:250px;text-align:center}
.service-icon{margin:0 auto;width:130px;height:130px;border-radius:50%;background:var(--white);border:4px solid var(--navy);display:flex;align-items:center;justify-content:center}
.service h3{margin-top:30px;font-family:"Raleway",sans-serif;font-weight:600;font-size:20px;color:var(--ink)}
.service p{margin-top:10px;font-size:12.5px;line-height:22px;color:var(--grey)}

/* process */
.process{left:0;top:1632px;width:1200px;height:517px;
  background:
    radial-gradient(ellipse at 75% 80%,rgba(20,70,140,.55) 0%,rgba(0,0,0,0) 60%),
    radial-gradient(ellipse at 55% 30%,#48addf 0%,#2f8fce 45%,#1c62aa 100%)}
.process-image{left:98px;top:1689px;width:410px;height:402px;border:4px solid var(--white);
  background:
    radial-gradient(ellipse at 30% 70%,rgba(255,190,110,.35) 0%,rgba(0,0,0,0) 45%),
    radial-gradient(ellipse at 65% 30%,rgba(140,200,255,.45) 0%,rgba(0,0,0,0) 50%),
    linear-gradient(160deg,#1f3f6a 0%,#4f76a2 40%,#2a3b5a 70%,#18223a 100%)}
.process-title{left:562px;top:1686px;font-family:"Raleway",sans-serif;font-weight:700;font-size:30px;color:var(--white)}
.process-text{left:562px;top:1742px;width:545px;font-size:12.5px;line-height:28px;color:var(--white)}
.process-sub{left:562px;top:1828px;font-weight:700;font-size:13px;color:var(--white)}
.profit-list{left:562px;top:1850px;list-style:none;font-size:12.5px;color:var(--white)}
.profit-list li{height:27.6px;display:flex;align-items:center;gap:12px}
.btn-ghost{left:562px;top:2051px;width:131px;height:36px;border-radius:18px;border:1.5px solid var(--white);color:var(--white);font-weight:700;font-size:12.5px;display:flex;align-items:center;justify-content:center}

/* team */
.team-title{left:0;top:2240px;width:1200px;text-align:center;font-family:"Raleway",sans-serif;font-weight:700;font-size:29px;color:var(--ink)}
.member{top:2322px;width:360px;text-align:center}
.portrait{margin:0 auto;width:246px;height:246px;border-radius:50%;border:6px solid #eceef1;box-shadow:0 0 0 1px #d5d9df}
.member h3{margin-top:20px;font-family:"Raleway",sans-serif;font-weight:700;font-size:18px;color:var(--ink)}
.member .role{margin-top:6px;font-style:italic;font-size:14px;color:var(--blue)}
.member p.bio{margin-top:8px;font-size:12.5px;line-height:24px;color:var(--grey);padding:0 24px}

/* footer */
.footer-curve{left:0;top:2770px;width:1200px;height:366px}
.footer-contact{top:2932px;display:flex;align-items:center;gap:16px;font-size:16px;color:var(--white)}
.ring-light{width:44px;height:44px;border-radius:50%;border:1.5px solid #8b8f96;display:flex;align-items:center;justify-content:center}
.footer-nav{left:0;top:3008px;width:1200px;text-align:center;font-family:"Raleway",sans-serif;font-size:16px;color:var(--white);word-spacing:4px}
.footer-rule{left:98px;top:3056px;width:1004px;height:1px;background:#3c3f44}
.copyright{left:98px;top:3084px;font-size:14px;color:var(--white)}
.social{left:933px;top:3078px;display:flex;gap:12px}
.social span{width:38px;height:38px;border-radius:50%;border:1.5px solid #d0d3d8}
</style>
</head>
<body>

<header class="abs site-header">
  <div class="abs brand"><span class="brand-dot"></span><span class="brand-name">Quorbelline</span></div>
  <div class="abs contact-top" style="left:712px">
    <span class="icon-ring"><svg width="16" height="16" viewBox="0 0 24 24"><path d="M6.6 10.8a15 15 0 0 0 6.6 6.6l2.2-2.2a1 1 0 0 1 1-.25 11.4 11.4 0 0 0 3.6.6 1 1 0 0 1 1 1V20a1 1 0 0 1-1 1A17 17 0 0 1 3 4a1 1 0 0 1 1-1h3.5a1 1 0 0 1 1 1 11.4 11.4 0 0 0 .6 3.6 1 1 0 0 1-.25 1z" fill="#2f9fd8"/></svg></span>
    <span>1 555 014 2730</span>
  </div>
  <div class="abs contact-top" style="left:904px">
    <span class="icon-ring"><svg width="16" height="12" viewBox="0 0 24 18"><rect x="1" y="1" width="22" height="16" rx="2" fill="#2f9fd8"/><path d="M1 2l11 8 11-8" stroke="#fff" stroke-width="2" fill="none"/></svg></span>
    <span>info@quorbelline.io</span>
  </div>
  <nav class="abs main-nav">
    <span>Home</span><span>About</span><span>Services</span><span>Press</span><span>Resources</span><span>Careers</span><span>Contact</span>
    <svg width="16" height="16" viewBox="0 0 24 24"><circle cx="10" cy="10" r="7" stroke="#1d1d1d" stroke-width="3" fill="none"/><path d="M15 15l7 7" stroke="#1d1d1d" stroke-width="3"/></svg>
  </nav>
</header>

<section class="abs hero" role="img" aria-label="Harbour city skyline with towers reflected on the water"></section>
<h1 class="abs hero-title">Digital Asset Management</h1>
<p class="abs hero-sub">Quorbelline is a cryptocurrency hedge fund that allow you to participate<br>in the hedge fund with cryptocurrency such as eth.</p>
<div class="abs btn-solid">GET MORE INFO</div>
<div class="abs slider-dots"><span class="on"></span><span></span><span></span><span></span></div>

<h2 class="abs welcome-title">WELCOME TO QUORBELLINE</h2>
<div class="abs welcome-text">
  <p>Quorbelline process and manages on hedge fund strategy models which invests in a diversified portfolio of blockchain tokens.</p>
  <p>Blockchain tokens are emerging which add a monetary incentive layer to p2p protocols and facilitate equity crowdfunding that anyone in the world can participate in. This means open source software developers can monetize their networks at the protocol level and users of the network are the equity owners of the network. For this conditions, returns will go to holders of the tokens.</p>
</div>
<div class="abs btn-outline" style="left:98px;top:963px;width:132px">READ MORE &gt;&gt;</div>
<div class="abs video-frame" role="img" aria-label="Video still of glowing blockchain network blocks">
  <div class="abs play"><svg width="60" height="60" viewBox="0 0 60 60"><path d="M24 18l18 12-18 12z" fill="#fff"/></svg></div>
</div>

<section class="abs services-band"></section>
<h2 class="abs services-title">WHAT WE DO</h2>

<div class="abs service" style="left:75px">
  <div class="service-icon"><svg width="56" height="56" viewBox="0 0 56 56"><path d="M28 8a14 14 0 0 0-8 25.5V40h16v-6.5A14 14 0 0 0 28 8z" fill="none" stroke="#2f9fd8" stroke-width="3.5"/><path d="M21 45h14M23 50h10" stroke="#2f9fd8" stroke-width="3.5"/></svg></div>
  <h3>Innovative</h3>
  <p>At Brisk Harbor we offer a variety of professional services specializing</p>
</div>
<div class="abs service" style="left:341px">
  <div class="service-icon"><svg width="60" height="56" viewBox="0 0 60 56"><path d="M6 6v42h50" stroke="#2f9fd8" stroke-width="3" fill="none"/><path d="M12 40l12-14 9 8 16-18" stroke="#2f9fd8" stroke-width="3.5" fill="none"/><path d="M42 14h9v9" stroke="#2f9fd8" stroke-width="3.5" fill="none"/></svg></div>
  <h3>Fund Strategy</h3>
  <p>At Brisk Harbor we offer a variety of professional services specializing</p>
</div>
<div class="abs service" style="left:608px">
  <div class="service-icon"><svg width="60" height="56" viewBox="0 0 60 56"><circle cx="22" cy="30" r="12" fill="none" stroke="#2f9fd8" stroke-width="7" stroke-dasharray="5 4"/><circle cx="22" cy="30" r="5" fill="#2f9fd8"/><circle cx="44" cy="16" r="7" fill="none" stroke="#2f9fd8" stroke-width="5" stroke-dasharray="3 3"/><circle cx="46" cy="40" r="6" fill="none" stroke="#2f9fd8" stroke-width="4" stroke-dasharray="3 3"/></svg></div>
  <h3>Asset Management</h3>
  <p>At Brisk Harbor we offer a variety of professional services specializing</p>
</div>
<div class="abs service" style="left:875px">
  <div class="service-icon"><svg width="60" height="50" viewBox="0 0 60 50"><circle cx="30" cy="14" r="9" fill="#2f9fd8"/><circle cx="12" cy="18" r="6" fill="#2f9fd8"/><circle cx="48" cy="18" r="6" fill="#2f9fd8"/><path d="M16 46a14 14 0 0 1 28 0z" fill="#2f9fd8"/><path d="M2 42a10 10 0 0 1 16-8v8zM58 42a10 10 0 0 0-16-8v8z" fill="#2f9fd8"/></svg></div>
  <h3>Crowdfunding</h3>
  <p>At Brisk Harbor we offer a variety of professional services specializing</p>
</div>
<div class="abs btn-outline" style="left:505px;top:1502px;width:188px;height:44px;border-radius:22px">VIEW MORE SERVICES</div>

<section class="abs process"></section>
<div class="abs process-image" role="img" aria-label="Photo of connected blockchain node blocks in blue light"></div>
<h2 class="abs process-title">HEDGE FUND MODEL PROCESS</h2>
<p class="abs process-text">Quorbelline run on closed-end fund （CEF）model which offers its shares to investors and utilize the fund to speculate and invest in the innovative blockchain tokens.</p>
<div class="abs process-sub">NET PROFIT DISTRIBUTION</div>
<ul class="abs profit-list">
  <li><svg width="12" height="10" viewBox="0 0 12 10"><path d="M1 5l3.5 3.5L11 1" stroke="#fff" stroke-width="2.2" fill="none"/></svg>50 % of net profit is distributed to investors</li>
  <li><svg width="12" height="10" viewBox="0 0 12 10"><path d="M1 5l3.5 3.5L11 1" stroke="#fff" stroke-width="2.2" fill="none"/></svg>0 – 5 % net profit &gt; 0% performance fee</li>
  <li><svg width="12" height="10" viewBox="0 0 12 10"><path d="M1 5l3.5 3.5L11 1" stroke="#fff" stroke-width="2.2" fill="none"/></svg>5 – 10% net profit &gt; 5% performance fee</li>
  <li><svg width="12" height="10" viewBox="0 0 12 10"><path d="M1 5l3.5 3.5L11 1" stroke="#fff" stroke-width="2.2" fill="none"/></svg>10-15 % net profit &gt; 13% performance fee</li>
  <li><svg width="12" height="10" viewBox="0 0 12 10"><path d="M1 5l3.5 3.5L11 1" stroke="#fff" stroke-width="2.2" fill="none"/></svg>&gt; 15% net profit &gt; 15% performance fee</li>
  <li><svg width="12" height="10" viewBox="0 0 12 10"><path d="M1 5l3.5 3.5L11 1" stroke="#fff" stroke-width="2.2" fill="none"/></svg>The remainder （50% minus performance fee, so at least 35%）is reinvested</li>
</ul>
<div class="abs btn-ghost">READ MORE</div>

<h2 class="abs team-title">EXECUTIVE TEAM</h2>
<div class="abs member" style="left:60px">
  <div class="portrait" role="img" aria-label="Portrait photo of the director" style="background:radial-gradient(circle at 50% 45%,#9b8573 0%,#6b5a4c 45%,#3b3430 100%)"></div>
  <h3>Dorvin Keltamara</h3>
  <div class="role">Director</div>
  <p class="bio">As a hedge fund manager, Keltamara is the Chief Executive Officer of Westfold Capital LLC, an investment manager of Ashcombe</p>
</div>
<div class="abs member" style="left:420px">
  <div class="portrait" role="img" aria-label="Portrait photo of the technical advisor" style="background:radial-gradient(circle at 50% 45%,#b59a80 0%,#a9b396 45%,#d4dcc4 100%)"></div>
  <h3>Jaleth Orrin</h3>
  <div class="role">Technical advisor</div>
  <p class="bio">Orrin has various experienced on cryptocurrency and blockchain technology. He created what was the world's 4th most valuable cryptocurrency</p>
</div>
<div class="abs member" style="left:780px">
  <div class="portrait" role="img" aria-label="Portrait photo of the marketing consultant" style="background:radial-gradient(circle at 50% 45%,#c49a80 0%,#a8422c 45%,#6a2618 100%)"></div>
  <h3>Casrin Velopharte</h3>
  <div class="role">Marketing Consultant</div>
  <p class="bio">Velopharte embeds a decade of experience in brand building, strategic planning, and marketing communication across the global</p>
</div>

<svg class="abs footer-curve" width="1200" height="366" viewBox="0 0 1200 366">
  <path d="M0 12 Q600 110 1200 12 L1200 366 L0 366 Z" fill="#1f2124"/>
  <path d="M40 18 Q600 100 1160 18 Q600 82 40 18 Z" fill="#2f9fd8"/>
</svg>
<div class="abs footer-contact" style="left:210px">
  <span class="ring-light"><svg width="14" height="18" viewBox="0 0 14 18"><path d="M7 1a6 6 0 0 0-6 6c0 4.5 6 10 6 10s6-5.5 6-10a6 6 0 0 0-6-6z" fill="#fff"/><circle cx="7" cy="7" r="2.2" fill="#1f2124"/></svg></span>
  <span style="font-size:14.5px;line-height:22px">Marlow Quay, 42, Vennick Road,<br>Eastbridge District, Port Alder.</span>
</div>
<div class="abs footer-contact" style="left:552px">
  <span class="ring-light"><svg width="16" height="16" viewBox="0 0 24 24"><path d="M6.6 10.8a15 15 0 0 0 6.6 6.6l2.2-2.2a1 1 0 0 1 1-.25 11.4 11.4 0 0 0 3.6.6 1 1 0 0 1 1 1V20a1 1 0 0 1-1 1A17 17 0 0 1 3 4a1 1 0 0 1 1-1h3.5a1 1 0 0 1 1 1 11.4 11.4 0 0 0 .6 3.6 1 1 0 0 1-.25 1z" fill="#fff"/></svg></span>
  <span>+1 555 014 2730</span>
</div>
<div class="abs footer-contact" style="left:774px">
  <span class="ring-light"><svg width="16" height="12" viewBox="0 0 24 18"><rect x="1" y="1" width="22" height="16" rx="2" fill="#fff"/><path d="M1 2l11 8 11-8" stroke="#1f2124" stroke-width="2" fill="none"/></svg></span>
  <span>info@quorbelline.io</span>
</div>
<nav class="abs footer-nav">Home &nbsp;| &nbsp;About &nbsp;| &nbsp;Services &nbsp;| &nbsp;Press &nbsp;| &nbsp;Resources &nbsp;| &nbsp;Careers &nbsp;| &nbsp;Contact</nav>
<div class="abs footer-rule"></div>
<div class="abs copyright">Copyrights © 2017, Quorbelline. All rights reserved.</div>
<div class="abs social"><span></span><span></span><span></span><span></span></div>

</body>
</html>
```